Flat bootstrap design for existing site

I'm looking for a modern flat design based around an existing logo. This has to be a custom design (no external templates), and implemented into a bootstrap framework.

The logo is attached as 2 versions - choose whichever you want, that flows better with whatever design you choose.

Added screenshots of the existing site (currently using the default bootstrap layouts). Please make your designs around those pages in the screenshots (i.e. the homepage only has the postal code input and the header). The active page has 3 screenshots, because I wanted to illustrate the other states that would be visible (in the table rows).

This is a moving/junk removal website, just for some context.

Here's some example websites (flat designs) that I like, just to give you an idea of what I'm after.

https://www.plimvora.com/
https://dacklow.com/
https://trevanu.com/
https://quobrintal.com/en/

Coding

Coded - Design and coding required

Number of Pages Required

5+ page

Colors

Designer to choose colors to be used in the design.

Requirements
Must have
• It must be a modern/simple flat design, that is built around the existing logo (attached).
• It has to be implemented using bootstrap.

```html
<!DOCTYPE html>
<html lang="en">
<head>
<meta charset="utf-8">
<title>Vantrel – Login</title>
<link rel="stylesheet" href="https://fonts.googleapis.com/css2?family=Open+Sans:wght@400;600;700&family=Poppins:wght@500;700&display=swap">
<style>
  :root {
    --sky: #4bc9f4;
    --sky-dark: #28a9d6;
    --link: #2a9fd3;
    --ink: #5f5f5f;
    --muted: #8c8c8c;
    --border: #7a7a7a;
    --white: #ffffff;
  }
  * { box-sizing: border-box; margin: 0; padding: 0; }
  html, body { width: 1200px; height: 406px; overflow: hidden; background: var(--white); }
  body { position: relative; font-family: "Open Sans", Arial, sans-serif; color: var(--ink); }

  .site-header { position: absolute; left: 0; top: 0; width: 1200px; height: 47px; background: var(--sky); }
  .brand { position: absolute; left: 99px; top: 0; height: 47px; display: flex; align-items: center; gap: 6px;
    font-family: "Poppins", Arial, sans-serif; font-weight: 700; font-size: 20px; color: var(--white); text-decoration: none; letter-spacing: 0.5px; }
  .brand-dot { width: 10px; height: 10px; border-radius: 50%; background: var(--white); }
  .main-nav { position: absolute; right: 0; top: 0; height: 47px; display: flex; padding-right: 91px; }
  .nav-link { display: flex; align-items: center; height: 47px; padding: 0 14px; color: var(--white);
    font-weight: 600; font-size: 14px; text-decoration: none; }
  .nav-link.is-active { background: var(--sky-dark); }

  .login-panel { position: absolute; left: 424px; top: 100px; width: 352px; }
  .login-title { position: absolute; left: 2px; top: 0; font-size: 19px; font-weight: 400; color: var(--ink); }
  .field-label { position: absolute; left: 0; font-size: 12px; color: var(--muted); }
  .field-input { position: absolute; left: 0; width: 352px; height: 25px; border: 1px solid var(--border); background: var(--white); }
  .remember { position: absolute; left: 0; top: 166px; display: flex; align-items: center; gap: 6px; font-size: 11px; color: var(--ink); }
  .login-button { position: absolute; left: 224px; top: 160px; width: 120px; height: 28px; border: none; border-radius: 14px;
    background: var(--sky); color: var(--white); font-family: "Poppins", Arial, sans-serif; font-weight: 700; font-size: 14px;
    box-shadow: 0 2px 0 var(--sky-dark); }
  .signup-hint { position: absolute; left: 0; top: 201px; font-size: 11px; color: var(--ink); }
  .signup-hint a { color: var(--link); font-weight: 600; text-decoration: none; margin-left: 6px; }
  .forgot-link { position: absolute; left: 241px; top: 200px; font-size: 12px; color: var(--link); text-decoration: none; }

  .site-footer { position: absolute; left: 0; top: 375px; width: 1200px; height: 31px; background: var(--sky);
    display: flex; align-items: center; justify-content: center; font-family: "Poppins", Arial, sans-serif;
    font-weight: 500; font-size: 11px; color: var(--white); }
</style>
</head>
<body>
  <header class="site-header">
    <a class="brand" href="#"><span class="brand-dot"></span>Vantrel</a>
    <nav class="main-nav">
      <a class="nav-link" href="#">Book</a>
      <a class="nav-link" href="#">How It Works</a>
      <a class="nav-link is-active" href="#">Become A Driver</a>
      <a class="nav-link" href="#">Sign In</a>
    </nav>
  </header>

  <main class="login-panel">
    <h1 class="login-title">Login</h1>
    <label class="field-label" style="top:40px" for="email">Email Address</label>
    <input class="field-input" style="top:63px" id="email" type="email">
    <label class="field-label" style="top:100px" for="password">Password</label>
    <input class="field-input" style="top:120px" id="password" type="password">
    <div class="remember">
      <svg width="10" height="10" viewBox="0 0 10 10" aria-hidden="true">
        <rect x="0.5" y="1.5" width="8" height="8" fill="none" stroke="#5f5f5f"/>
        <path d="M2.5 5l2 2 5-6" fill="none" stroke="#5f5f5f" stroke-width="1.3"/>
      </svg>
      keep me logged in
    </div>
    <button class="login-button" type="submit">LOGIN</button>
    <p class="signup-hint">Need an account?<a href="#">Sign Up</a></p>
    <a class="forgot-link" href="#">Forgot Password?</a>
  </main>

  <footer class="site-footer">© 2017 Vantrel. All Rights Reserved.</footer>
</body>
</html>
```